BOLD & MINIMALIST DESIGN NEEDED

We want a very bold but minimalistic business card design that is impactful and utilizes both sides of the business card. Our current logo is included for your use.

We want bold fonts and good use of negative space. We don't want the logo to overpower the design.

Target Market(s)

Professionals who are building new commercial buildings.

Industry/Entity Type

Construction

Contact Information for Business Card

Name, Title, email, office phone, cell phone, website

Font styles to use
Serif
Sans Serif

Requirements
Must have
• Bold design!

```html
<!DOCTYPE html>
<html lang="en">
<head>
<meta charset="utf-8">
<title>Ridgecrest – Business Card</title>
<link href="https://fonts.googleapis.com/css2?family=Arimo:wght@400;700&display=swap" rel="stylesheet">
<style>
  :root {
    --backdrop: #e4e4e4;
    --card-front: #ffffff;
    --card-back: #2a2a2a;
    --ink: #111111;
    --ink-soft: #444444;
    --accent: #7dc242;
    --emboss: #3b3b3b;
  }
  * { margin: 0; padding: 0; box-sizing: border-box; }
  html, body { width: 1200px; height: 1200px; overflow: hidden; }
  body {
    background: var(--backdrop);
    font-family: "Arimo", Arial, sans-serif;
    position: relative;
  }
  .card {
    position: absolute;
    width: 689px;
    height: 394px;
  }
  .card--front {
    left: 267px;
    top: 159px;
    background: var(--card-front);
    border: 1px solid #cfcfcf;
  }
  .card--back {
    left: 262px;
    top: 653px;
    background: var(--card-back);
  }
  .brand {
    position: absolute;
    left: 40px;
    top: 58px;
    display: flex;
    align-items: center;
    gap: 10px;
  }
  .brand__mark {
    width: 16px;
    height: 16px;
    background: var(--accent);
  }
  .brand__name {
    font-weight: 700;
    font-size: 38px;
    letter-spacing: 0.5px;
    color: var(--ink);
    line-height: 1;
  }
  .person {
    position: absolute;
    left: 40px;
    top: 178px;
  }
  .person__name {
    font-weight: 700;
    font-size: 26px;
    color: var(--ink);
    line-height: 1;
  }
  .person__title {
    margin-top: 8px;
    font-size: 15px;
    color: var(--accent);
  }
  .contacts {
    position: absolute;
    left: 40px;
    top: 268px;
    list-style: none;
  }
  .contacts li {
    display: flex;
    align-items: center;
    gap: 13px;
    height: 20.5px;
    font-size: 16px;
    color: var(--ink-soft);
  }
  .contacts svg { width: 14px; height: 14px; fill: var(--ink); flex: none; }
  .back-brand {
    position: absolute;
    left: 0; right: 0;
    top: 50%;
    transform: translateY(-50%);
    display: flex;
    justify-content: center;
    align-items: center;
    gap: 16px;
  }
  .back-brand__mark {
    width: 26px;
    height: 26px;
    background: var(--emboss);
  }
  .back-brand__name {
    font-weight: 700;
    font-size: 60px;
    color: var(--emboss);
    letter-spacing: 1px;
    line-height: 1;
  }
</style>
</head>
<body>
  <section class="card card--front">
    <div class="brand">
      <span class="brand__mark"></span>
      <span class="brand__name">RIDGECREST</span>
    </div>
    <div class="person">
      <p class="person__name">DANIEL BROOKS</p>
      <p class="person__title">President</p>
    </div>
    <ul class="contacts">
      <li>
        <svg viewBox="0 0 24 24" aria-hidden="true"><path d="M6.6 10.8a15.1 15.1 0 0 0 6.6 6.6l2.2-2.2a1 1 0 0 1 1-.25 11.4 11.4 0 0 0 3.6.57 1 1 0 0 1 1 1V20a1 1 0 0 1-1 1A17 17 0 0 1 3 4a1 1 0 0 1 1-1h3.5a1 1 0 0 1 1 1c0 1.25.2 2.45.57 3.57a1 1 0 0 1-.25 1z"/></svg>
        555-210-4837
      </li>
      <li>
        <svg viewBox="0 0 24 24" aria-hidden="true"><path d="M7 1h10a2 2 0 0 1 2 2v18a2 2 0 0 1-2 2H7a2 2 0 0 1-2-2V3a2 2 0 0 1 2-2zm0 3v14h10V4z"/></svg>
        555-318-9062
      </li>
      <li>
        <svg viewBox="0 0 24 24" aria-hidden="true"><path d="M2 5h20v14H2zm2 2v.5l8 5 8-5V7zm0 3v7h16v-7l-8 5z"/></svg>
        info@ridgecrest.com
      </li>
      <li>
        <svg viewBox="0 0 24 24" aria-hidden="true"><circle cx="12" cy="12" r="10"/><path d="M8 6l3 2-1 3 3 2v4l-3-2-3-4zM15 6l3 3-2 2z" fill="#ffffff"/></svg>
        www.ridgecrest.com
      </li>
    </ul>
  </section>

  <section class="card card--back">
    <div class="back-brand">
      <span class="back-brand__mark"></span>
      <span class="back-brand__name">RIDGECREST</span>
    </div>
  </section>
</body>
</html>
```